Photographer's price list

I am a photographer who runs a studio (Marrowfield Studio) and need to have a document to send clients detailing my packages (collections) and prices. I have written the text in a word document and need a designer to lay it out for me using my logo and two specific fonts: DejaVu Sans and LainieDaySH.

The look should be clean and modern and keep in the same style as my logo. I will primarily be using the final product as a PDF file to email to potential clients. It should stay black and white.

I would also like to be able to update the text myself as my prices and packages change. So I would like a PSD file.

I think I would like for the document to be in landscape format with "Collections" on one side and A la Carte on the other, but I am open to other ideas.

As for sizing, it should be a standard size so that clients can print it out if they like.

Industry/Entity Type

Landscape

Requirements
Must have
• my logo
fonts: DejaVu and LainieDaySH
Easy to email
Easy to display on one page upon opening
Standard size so that printing from a home computer is easy to do.

```html
<!DOCTYPE html>
<html lang="en">
<head>
<meta charset="utf-8">
<title>Marrowfield Studio – 2013 Photography Collections</title>
<link rel="stylesheet" href="https://fonts.googleapis.com/css2?family=Noto+Sans:wght@400;700&family=Parisienne&display=swap">
<style>
  :root {
    --backdrop: #6b6b6b;
    --paper: #d2d2d4;
    --ink: #111111;
    --panel: #222222;
    --panel-text: #b9b9b9;
    --panel-title: #d8d8d8;
    --white: #ffffff;
    --photo-dark: #3a3a3a;
    --photo-light: #bdbdbd;
  }
  * { box-sizing: border-box; margin: 0; padding: 0; }
  html, body { width: 775px; height: 1200px; overflow: hidden; }
  body {
    background: var(--backdrop);
    position: relative;
    font-family: "Noto Sans", "DejaVu Sans", sans-serif;
    color: var(--ink);
  }
  .page {
    position: absolute;
    left: 17px;
    width: 741px;
    background: var(--paper);
    overflow: hidden;
  }
  .cover { top: 17px; height: 573px; }
  .pricing { top: 610px; height: 573px; }

  /* cover */
  .cover__bar { position: absolute; left: 336px; top: 0; width: 34px; height: 174px; background: var(--ink); }
  .cover__photo {
    position: absolute; left: 370px; top: 0; width: 371px; height: 174px;
    background: linear-gradient(100deg, var(--photo-dark) 0%, var(--photo-light) 45%, #e6e6e6 70%, var(--photo-light) 100%);
  }
  .cover__band { position: absolute; left: 0; bottom: 0; width: 100%; height: 64px; background: var(--ink); }
  .brand {
    position: absolute; left: 541px; top: 210px; width: 152px; height: 152px;
    border-radius: 50%; background: var(--white);
    display: flex; align-items: center; justify-content: center;
  }
  .brand__name { font-size: 11px; letter-spacing: 1.5px; text-transform: uppercase; color: var(--ink); }
  .cover__year {
    position: absolute; right: 40px; top: 400px;
    font-family: "Parisienne", cursive; font-size: 40px; line-height: 44px; color: var(--ink);
  }
  .cover__title {
    position: absolute; right: 40px; top: 448px;
    font-family: "Parisienne", cursive; font-size: 33px; line-height: 36px; color: var(--ink);
  }
  .contact {
    position: absolute; left: 115px; top: 435px; width: 175px;
    text-align: center; font-size: 10px; line-height: 12.5px;
  }
  .contact__label { font-weight: 700; }

  /* pricing page */
  .collection {
    position: absolute; left: 30px; width: 310px; height: 96px;
    background: var(--panel); border-radius: 8px; overflow: hidden;
    text-align: center; color: var(--panel-text);
  }
  .collection__ribbon {
    position: absolute; left: -14px; top: 10px; width: 90px; height: 16px;
    transform: rotate(-22deg);
    background: linear-gradient(90deg, #f2f2f2 0%, #c8c8c8 55%, #5a5a5a 100%);
    display: flex; align-items: center; padding-left: 22px;
    font-size: 10px; font-weight: 700; color: var(--ink);
  }
  .collection__name {
    font-family: "Parisienne", cursive; font-size: 20px; color: var(--panel-title);
    line-height: 20px; margin-top: 5px; padding-left: 20px;
  }
  .collection__text { font-size: 8.2px; line-height: 9.8px; padding: 1px 18px 0 34px; }

  .includes { position: absolute; left: 40px; top: 462px; width: 290px; text-align: center; }
  .script-heading { font-family: "Parisienne", cursive; font-size: 19px; line-height: 22px; color: var(--ink); }
  .includes__text { font-size: 7.8px; line-height: 9.4px; }

  .carte { position: absolute; left: 410px; width: 310px; text-align: center; }
  .carte__text { font-size: 9px; line-height: 10.6px; }
  .price { font-family: "Parisienne", cursive; font-size: 12px; }
</style>
</head>
<body>

<section class="page cover">
  <div class="cover__bar"></div>
  <div class="cover__photo" role="img" aria-label="Black and white family portrait photograph"></div>
  <div class="brand"><span class="brand__name">Marrowfield Studio</span></div>
  <div class="cover__year">2013</div>
  <div class="cover__title">photography collections</div>
  <div class="contact">
    <p class="contact__label">Contact Information</p>
    <p>Clara Wendt</p>
    <p>+49 170 555 0142</p>
    <p>Lindenau, 04177</p>
    <p>Germany</p>
  </div>
  <div class="cover__band"></div>
</section>

<section class="page pricing">
  <article class="collection" style="top:36px">
    <div class="collection__ribbon">300 €</div>
    <h2 class="collection__name">Collection 1</h2>
    <p class="collection__text">Your favorite five images from the session will be professionally edited and presented to you on disk as high resolution jpegs.</p>
  </article>
  <article class="collection" style="top:143px">
    <div class="collection__ribbon">400 €</div>
    <h2 class="collection__name">Collection 2</h2>
    <p class="collection__text">Your favorite ten images from the session will be professionally edited and given to you on disk as high resolution jpegs.<br>Your favorite image from the session will be professionally printed for you (20x30cm) on Velmoor paper, Clara's favorite for portraits.</p>
  </article>
  <article class="collection" style="top:249px">
    <div class="collection__ribbon">500 €</div>
    <h2 class="collection__name">Collection 3</h2>
    <p class="collection__text">Your favorite fifteen images from the session will be professionally edited and presented to you on disk as high resolution jpegs.<br>Your favorite two images from the session will be professionally printed for you (20x30cm) on Velmoor paper, Clara's favorite for portraits.</p>
  </article>
  <article class="collection" style="top:356px">
    <div class="collection__ribbon">600 €</div>
    <h2 class="collection__name">Collection 4</h2>
    <p class="collection__text"><u>ALL</u> presented images from the session will be professionally edited and presented to you on disk as high resolution jpegs (approximately 40+ images).<br>Your favorite <u>two</u> images from the session will be professionally printed for you (20x30cm) on Velmoor paper, Clara's favorite for portraits.</p>
  </article>

  <div class="includes">
    <h3 class="script-heading">all collections include:</h3>
    <p class="includes__text">One to two hour portrait session with photographer in location of your choice (unlimited time if necessary!)<br>Clara will create a presentation video with hand-selected music and custom editing, which tells your story, highlights the best images, and reveals the connections within your family.<br>An online gallery for viewing and ordering helps you share your images with family and friends.</p>
  </div>

  <div class="carte" style="top:27px">
    <h3 class="script-heading">a la carte pricing</h3>
    <p class="carte__text">These products may be purchased separately to complement your collection. A consultation with Clara will help you decide which products are best for gifts and for your home.</p>
  </div>
  <div class="carte" style="top:107px">
    <h3 class="script-heading">high resolution digital images</h3>
    <p class="carte__text">Perfect if you just need to add “one more image” to your collection!<br>High-resolution jpeg file <span class="price">25 €</span> each</p>
  </div>
  <div class="carte" style="top:179px">
    <h3 class="script-heading">matt prints</h3>
    <p class="carte__text">20x30 cm and smaller <span class="price">25 €</span><br>Each print is professionally edited, printed on archival photo paper.<br>Purchase includes the JPEG file for your personal digital use.</p>
  </div>
  <div class="carte" style="top:255px">
    <h3 class="script-heading">velmoor prints</h3>
    <p class="carte__text">Prints on Velmoor (watercolor) paper are Clara's favorite for large format color prints<br>30x40 cm <span class="price">45 €</span></p>
  </div>
  <div class="carte" style="top:331px">
    <h3 class="script-heading">canvas prints</h3>
    <p class="carte__text">Ready-to-hang, stretched canvas wall art of your favorite images<br>30x40 cm <span class="price">100 €</span></p>
  </div>
  <div class="carte" style="top:386px">
    <h3 class="script-heading">framed + matted prints</h3>
    <p class="carte__text">Beautiful Velmoor prints finished with wide mats and simple, elegant frames of your choice<br>30x40 inch <span class="price">350 €</span></p>
  </div>
  <div class="carte" style="top:455px">
    <h3 class="script-heading">custom designed albums</h3>
    <p class="carte__text">Images from your session are selected for the custom design of an album and bound in a book for a modern presentation of your images. There are a number of cover choices for the classic flush-mount and beautifully crafted albums. A great way to display all of your favorite images from your session on your coffee table.<br>Prices begin at <span class="price">700 €</span></p>
  </div>
</section>

</body>
</html>
```